Counseling Practice Business Card

I need a professional looking business card incorporating my new logo that was just completed. Card needs to incorporate my name and title, description of my specialty, my address, my phone number, my fax number, my email and my website URL. I need to be able to choose design on/with different paper colors and textures.
I do not have a lot of business card ideas so I am open to anything but I want bold,sharp, clear card without additional designs other than my logo (see attached file info). I am open to different color backgrounds or paper colors including black. I do not like traditional brackets around area codes in phone number or dashes between numbers in phone number. Am open to other ways of presenting including periods between numbers as appropriate. I do not know enough to know what I like yet but I want card to coordinate and work together with my logo. My practice emphasizes natural mental health interventions so any use of color (with background paper color or the blue and green in my logo) that elicits nature is nice. In addition to black, any natural brown or wood looking background might be desirable also. Most of the offerings so far look very similar and boring.

Target Market(s)

Potential therapy clients and other professionals

Contact Information for Business Card

Card information:
Gerald M. Whitcombe, Ph.D.
Licensed Clinical Psychologist
Integrative Health Coach
4812 Marlowe Ridge Blvd SE
Suite 310
Duluth, GA 30096
(770) 415-2983 phone
(770) 581-4096 fax
drgeraldwhitcombe@quillmarsh.net
brightfernwellness.net

Font styles to use
Serif
Sans Serif
Other font styles liked:
• anything that you think looks crisp, clear and easily readable

Requirements
Must have
• Any color used should coordinate with my logo design (see attached files).
• Card should be printed horizontally so top and bottom are longest sides of rectangle.
• Background color or paper color should complement and highlight logo. Do not like a white background. black, grey, brown or any color my logo would blend well with.
Nice to have
• I would like designer to utilize color to highlight letters/name or phone-fax-web symbols.
• Bottom edge of card could be highlighted if appropriate to an idea.
Should not have
• I would NOT want the card to have a pure white background at all.
• No clear cards.
• Cards should be oriented with long sides on bottom and top, NOT sides. DO NOT LIKE THIS THIN TALL ORIENTATION.

```html
<!DOCTYPE html>
<html lang="en">
<head>
<meta charset="utf-8">
<title>Brightfern Wellness – Business Card</title>
<link href="https://fonts.googleapis.com/css2?family=Open+Sans:wght@400;700&display=swap" rel="stylesheet">
<style>
  :root {
    --stage: #4a4a4c;
    --card: #141416;
    --green: #0f7a36;
    --blue: #2b73c0;
    --white: #ffffff;
    --grey-text: #c9c9c9;
    --divider: #5a5a5e;
  }
  * { margin: 0; padding: 0; box-sizing: border-box; }
  html, body { width: 1200px; height: 840px; overflow: hidden; }
  body {
    background: var(--stage);
    font-family: "Open Sans", Arial, sans-serif;
    position: relative;
  }
  .card {
    position: absolute;
    width: 620px;
    height: 354px;
    background: var(--card);
    border-radius: 4px;
    box-shadow: 0 10px 28px rgba(0,0,0,.45);
    overflow: hidden;
  }
  .card--back { left: 100px; top: 50px; }
  .card--front { left: 480px; top: 436px; }

  .brand {
    display: flex;
    align-items: center;
    gap: 12px;
    color: var(--blue);
    font-weight: 700;
    white-space: nowrap;
  }
  .brand__dot {
    width: 18px; height: 18px;
    border-radius: 50%;
    background: var(--green);
    flex: none;
  }
  .card--back .brand {
    position: absolute;
    left: 50%; top: 50%;
    transform: translate(-50%, -50%);
    font-size: 34px;
  }
  .card--front .brand {
    position: absolute;
    left: 30px; top: 270px;
    font-size: 23px;
  }

  .band { position: absolute; inset: 0; }

  .identity {
    position: absolute;
    right: 24px; top: 22px;
    text-align: right;
    color: var(--white);
  }
  .identity__name {
    font-size: 19px;
    font-weight: 700;
    text-transform: uppercase;
    letter-spacing: .2px;
  }
  .identity__title { font-size: 14px; line-height: 1.3; }

  .divider {
    position: absolute;
    left: 312px; top: 160px;
    width: 1px; height: 170px;
    background: var(--divider);
  }
  .contact {
    position: absolute;
    left: 332px; top: 168px;
    color: var(--grey-text);
    font-size: 13px;
    line-height: 1.45;
    list-style: none;
  }
  .contact__address { margin-bottom: 6px; }
  .contact__row { display: flex; align-items: center; gap: 8px; }
  .contact__icon { width: 13px; height: 13px; flex: none; fill: var(--blue); }
</style>
</head>
<body>

<section class="card card--back" aria-label="Card back">
  <div class="brand"><span class="brand__dot"></span>Brightfern Wellness</div>
</section>

<section class="card card--front" aria-label="Card front">
  <svg class="band" viewBox="0 0 620 354" preserveAspectRatio="none" aria-hidden="true">
    <path d="M0,0 H620 V108 Q300,140 0,212 Z" fill="var(--green)"/>
    <path d="M0,212 Q300,140 620,108 V122 Q300,158 0,224 Z" fill="var(--blue)"/>
  </svg>

  <div class="identity">
    <p class="identity__name">Gerald M. Whitcombe, Ph.D.</p>
    <p class="identity__title">Licensed Clinical Psychologist</p>
    <p class="identity__title">Integrative Health Coach</p>
  </div>

  <div class="brand"><span class="brand__dot"></span>Brightfern Wellness</div>

  <div class="divider"></div>

  <ul class="contact">
    <li class="contact__address">4812 Marlowe Ridge Blvd SE<br>Suite 310<br>Duluth, GA 30096</li>
    <li class="contact__row">
      <svg class="contact__icon" viewBox="0 0 16 16" aria-hidden="true"><path d="M3 1h3l1.5 4-2 1.3a9 9 0 0 0 4.2 4.2L11 8.5l4 1.5v3a2 2 0 0 1-2 2A13 13 0 0 1 1 3a2 2 0 0 1 2-2z"/></svg>
      (770) 415-2983
    </li>
    <li class="contact__row">
      <svg class="contact__icon" viewBox="0 0 16 16" aria-hidden="true"><path d="M4 1h6v4H4zM1 6h14v7h-3v2H4v-2H1zM5 10v4h6v-4z"/></svg>
      (770) 581-4096
    </li>
    <li class="contact__row">
      <svg class="contact__icon" viewBox="0 0 16 16" aria-hidden="true"><path d="M1 3h14v10H1zM2 4l6 5 6-5v1.3L8 10.3 2 5.3z" fill-rule="evenodd"/></svg>
      drgeraldwhitcombe@quillmarsh.net
    </li>
    <li class="contact__row">
      <svg class="contact__icon" viewBox="0 0 16 16" aria-hidden="true"><circle cx="8" cy="8" r="7"/></svg>
      www.brightfernwellness.net
    </li>
  </ul>
</section>

</body>
</html>
```